Business Card for Coastal Tundrabridge Advisory

We need a business card for Coastal Tundrabridge Advisory. The company website address is provided below. The company logo is attached. We provide specialized permafrost services to the mining, transportation, and oil & gas industries. The card should be prepared for:
Matthias Korhonen, PhD.
Coastal Tundrabridge Advisory
PO Box 418259
Quillwater, Alaska 99642
Direct: +1-907-555-0143
Email: mkorhonen@tundrabridgeadvisory.example
Website: www.coastaltundrabridgeadvisory.example

```html
<!DOCTYPE html>
<html lang="en">
<head>
<meta charset="utf-8">
<title>Coastal Tundrabridge Advisory – Business Card</title>
<link href="https://fonts.googleapis.com/css2?family=Montserrat:wght@400;500;600;700&display=swap" rel="stylesheet">
<style>
  :root {
    --stage: #3b3532;
    --card-light: #ffffff;
    --card-dark: #151515;
    --ink: #1c2129;
    --ink-soft: #4a4f57;
    --rule: #3a3f46;
    --on-dark: #f4f4f4;
  }
  * { margin: 0; padding: 0; box-sizing: border-box; }
  html, body {
    width: 1200px; height: 786px; overflow: hidden;
    background: var(--stage);
    font-family: "Montserrat", sans-serif;
  }
  .stage {
    position: relative; width: 1200px; height: 786px;
  }
  .card {
    position: absolute; top: 245px;
    width: 520px; height: 297px;
    box-shadow: 0 8px 24px rgba(0,0,0,.35);
  }
  .card--front { left: 60px; background: var(--card-light); color: var(--ink); }
  .card--back  { left: 620px; background: var(--card-dark); color: var(--on-dark);
    display: flex; align-items: center; justify-content: center; }

  .wordmark {
    font-weight: 600; letter-spacing: .02em; white-space: nowrap;
  }
  .card--front .wordmark {
    position: absolute; left: 40px; top: 42px; font-size: 21px; color: var(--ink);
  }
  .card--back .wordmark { font-size: 25px; color: var(--on-dark); }

  .rule { position: absolute; height: 1px; background: var(--rule); }
  .rule--top { left: 40px; right: 40px; top: 100px; }
  .rule--name { left: 40px; width: 220px; top: 178px; }

  .person { position: absolute; left: 40px; top: 128px; }
  .person__name { font-size: 19px; font-weight: 700; color: var(--ink); }
  .person__title { font-size: 11px; font-weight: 400; color: var(--ink-soft); margin-top: 3px; }

  .address {
    position: absolute; left: 300px; top: 128px;
    padding-left: 12px; border-left: 1px solid var(--rule);
    font-size: 11px; line-height: 1.5; color: var(--ink-soft);
  }

  .contacts { position: absolute; left: 40px; top: 198px; list-style: none; }
  .contacts li {
    display: flex; align-items: center; gap: 9px;
    font-size: 11px; line-height: 1; color: var(--ink-soft); height: 22px;
  }
  .contacts svg { width: 11px; height: 11px; fill: var(--ink); flex: none; }
</style>
</head>
<body>
<main class="stage">
  <section class="card card--front">
    <div class="wordmark">Coastal Tundrabridge Advisory</div>
    <div class="rule rule--top"></div>

    <div class="person">
      <div class="person__name">Matthias Korhonen, PhD.</div>
      <div class="person__title">CEO &amp; Founder</div>
    </div>
    <div class="rule rule--name"></div>

    <div class="address">
      PO Box 418259<br>
      Quillwater, Alaska 99642
    </div>

    <ul class="contacts">
      <li>
        <svg viewBox="0 0 12 12" aria-hidden="true"><path d="M2.5 0.8l2 2.2-1 1.3c.7 1.5 1.7 2.5 3.2 3.2l1.3-1 2.2 2-1 2.1C5 10.6 1.4 7 .4 1.8z"/></svg>
        +1-907-555-0143
      </li>
      <li>
        <svg viewBox="0 0 12 12" aria-hidden="true"><path d="M0 2h12v8H0z M0.8 2.6L6 6.6l5.2-4" fill="var(--ink)"/><path d="M1 3l5 3.6L11 3" stroke="#fff" stroke-width="1" fill="none"/></svg>
        mkorhonen@tundrabridgeadvisory.example
      </li>
      <li>
        <svg viewBox="0 0 12 12" aria-hidden="true"><circle cx="6" cy="6" r="5.5"/><path d="M1 6h10M6 .5c-2 2.5-2 8.5 0 11M6 .5c2 2.5 2 8.5 0 11" stroke="#fff" stroke-width=".8" fill="none"/></svg>
        www.coastaltundrabridgeadvisory.example
      </li>
    </ul>
  </section>

  <section class="card card--back">
    <div class="wordmark">Coastal Tundrabridge Advisory</div>
  </section>
</main>
</body>
</html>
```